Velmora Cabinets Letter Head and Email Signature

Hi
I would love a design package for a letterhead, email signature, even update my business card if you like if you can come up with a great idea for my new high end cabinet shop. Velmora Cabinets brings timeless craftsmanship to modern interiors, specializing in high end, custom cabinetry designed for architects and interior designers.

Target Market(s)

high end, luxury market

Industry/Entity Type

cabinet making

Requirements
Must have
• my colours of logo as the theme

```html
<!DOCTYPE html>
<html lang="en">
<head>
<meta charset="utf-8">
<title>Velmora Cabinets Stationery</title>
<link href="https://fonts.googleapis.com/css2?family=Lato:wght@400&family=Montserrat:wght@400;500;600&display=swap" rel="stylesheet">
<style>
  :root {
    --backdrop: #adadad;
    --paper: #ffffff;
    --ink: #1c1c1c;
    --body-ink: #4a4a4a;
    --brand-green: #4a7d3e;
    --card-black: #181818;
    --card-text: #f2f2f2;
    --mark-grey: #d9d9d9;
  }
  * { margin: 0; padding: 0; box-sizing: border-box; }
  html, body { width: 1200px; height: 795px; overflow: hidden; }
  body { background: var(--backdrop); font-family: 'Montserrat', sans-serif; }
  .stage { position: relative; width: 1200px; height: 795px; }

  .brand-name {
    font-family: 'Montserrat', sans-serif;
    font-weight: 500;
    line-height: 1.05;
    letter-spacing: 0.12em;
    text-transform: uppercase;
  }
  .icon { display: inline-block; vertical-align: middle; }

  /* Letterhead */
  .letterhead {
    position: absolute; left: 160px; top: 137px;
    width: 369px; height: 521px; background: var(--paper);
  }
  .letterhead .brand-name {
    position: absolute; left: 35px; top: 24px;
    font-size: 14px; color: var(--brand-green);
  }
  .letterhead .contact {
    position: absolute; left: 227px; top: 24px;
    border-left: 1px solid var(--brand-green);
    padding-left: 9px; font-size: 6.6px; color: var(--ink);
    line-height: 9px;
  }
  .letterhead .contact .icon { width: 6px; height: 6px; margin-right: 2px; margin-top: -1px; }
  .recipient { position: absolute; left: 35px; top: 122px; font-family: 'Lato', sans-serif; color: var(--body-ink); }
  .recipient .name { font-size: 7px; color: var(--ink); line-height: 11px; }
  .recipient .line { font-size: 5.2px; line-height: 9px; }
  .letter-body {
    position: absolute; left: 35px; top: 185px; width: 300px;
    font-family: 'Lato', sans-serif; font-size: 5.3px; line-height: 9px;
    color: var(--body-ink); text-align: justify;
  }
  .letter-body p { margin-bottom: 8px; }
  .sign-off { position: absolute; left: 35px; top: 386px; font-family: 'Lato', sans-serif; color: var(--body-ink); }
  .sign-off .closing { font-size: 6px; }
  .sign-off .signer { font-size: 7px; margin-top: 22px; }

  /* Email signature */
  .email-signature {
    position: absolute; left: 587px; top: 109px;
    width: 453px; height: 164px; background: var(--paper);
  }
  .email-signature .brand-name {
    position: absolute; left: 40px; top: 60px;
    font-size: 17px; color: var(--brand-green);
  }
  .signature-divider {
    position: absolute; left: 226px; top: 37px; width: 1px; height: 90px;
    background: var(--brand-green);
  }
  .person { position: absolute; }
  .person .full-name { font-weight: 600; color: var(--brand-green); line-height: 1; }
  .person .role { color: var(--ink); }
  .person .details { list-style: none; color: var(--ink); }
  .email-signature .person { left: 250px; top: 34px; }
  .email-signature .full-name { font-size: 19px; }
  .email-signature .role { font-size: 11px; margin-top: 5px; }
  .email-signature .details { margin-top: 14px; font-size: 11px; line-height: 16px; }
  .email-signature .details .icon { width: 9px; height: 9px; margin-right: 5px; margin-top: -2px; }

  /* Business cards */
  .business-card {
    position: absolute; left: 587px; width: 313px; height: 179px;
    background: var(--card-black); border-radius: 10px;
  }
  .card-front { top: 301px; }
  .card-front .brand-name {
    position: absolute; left: 16px; top: 73px;
    font-size: 13px; color: var(--brand-green);
  }
  .card-front .signature-divider { left: 156px; top: 54px; height: 72px; }
  .card-front .person { left: 167px; top: 52px; }
  .card-front .full-name { font-size: 14px; }
  .card-front .role { font-size: 8.5px; margin-top: 4px; color: var(--card-text); }
  .card-front .details { margin-top: 11px; font-size: 8.5px; line-height: 12.5px; color: var(--card-text); }
  .card-front .details .icon { width: 7px; height: 7px; margin-right: 4px; margin-top: -2px; }

  .card-back { top: 508px; }
  .card-back .brand-name {
    position: absolute; left: 0; right: 0; top: 66px;
    text-align: center; font-size: 22px; color: var(--mark-grey);
    letter-spacing: 0.16em;
  }
</style>
</head>
<body>
<main class="stage">

  <section class="letterhead">
    <div class="brand-name">Velmora<br>Cabinets</div>
    <ul class="contact" style="list-style:none">
      <li><svg class="icon" viewBox="0 0 10 10"><path d="M1 4c2-3 6-3 8 0l-1.5 1-1-1.2h-3L2.5 5z M2.5 5.5h5l1 3.5h-7z" fill="var(--brand-green)"/></svg>0412558301</li>
      <li><svg class="icon" viewBox="0 0 10 10"><rect x="0.5" y="2" width="9" height="6" fill="var(--brand-green)"/><path d="M0.5 2l4.5 3.5 4.5-3.5" stroke="#fff" stroke-width="0.8" fill="none"/></svg>info@velmoracabinets.com.au</li>
      <li><svg class="icon" viewBox="0 0 10 10"><circle cx="5" cy="5" r="3.8" fill="none" stroke="var(--brand-green)" stroke-width="1.2"/></svg>@velmora.cabinets</li>
    </ul>

    <div class="recipient">
      <div class="name">MAREN WHITLOCK</div>
      <div class="line">Chief Executive Officer</div>
      <div class="line">City/State, Zip Code</div>
    </div>

    <div class="letter-body">
      <p>Thank you for considering Velmora Cabinets for your upcoming residence. Our workshop builds every piece by hand, pairing timeless joinery with modern finishes to suit each interior. We work closely with architects and interior designers from the first sketch, refining proportions, timber selection and hardware until every detail feels considered. Each cabinet is measured on site, crafted in our studio and installed by the same team, so the finished work matches the drawings exactly and stands the test of daily life.</p>
      <p>Enclosed you will find our proposal for the kitchen, butler's pantry and library joinery, along with finish samples in oak, walnut and painted lacquer. Pricing reflects solid timber carcasses, soft close hardware and integrated lighting throughout. We would welcome the chance to walk you through the details at our showroom or on site at a time that suits you.</p>
      <p>Once the design is approved, we will confirm a production schedule and keep you informed at every stage of the build. Our aim is simple: cabinetry that looks beautiful on the day it is installed and only grows richer with age. Please do not hesitate to contact me with any questions about materials, timing or the scope of works. We look forward to working with you.</p>
    </div>

    <div class="sign-off">
      <div class="closing">Sincerely,</div>
      <div class="signer">Elise Harrow</div>
    </div>
  </section>

  <section class="email-signature">
    <div class="brand-name">Velmora<br>Cabinets</div>
    <div class="signature-divider"></div>
    <div class="person">
      <div class="full-name">Rowan Ashdale</div>
      <div class="role">Director Craftsman</div>
      <ul class="details">
        <li><svg class="icon" viewBox="0 0 10 10"><path d="M1 4c2-3 6-3 8 0l-1.5 1-1-1.2h-3L2.5 5z M2.5 5.5h5l1 3.5h-7z" fill="var(--brand-green)"/></svg>0412558301</li>
        <li><svg class="icon" viewBox="0 0 10 10"><rect x="0.5" y="2" width="9" height="6" fill="var(--brand-green)"/><path d="M0.5 2l4.5 3.5 4.5-3.5" stroke="#fff" stroke-width="0.8" fill="none"/></svg>info@velmoracabinets.com.au</li>
        <li><svg class="icon" viewBox="0 0 10 10"><circle cx="5" cy="5" r="3.8" fill="none" stroke="var(--brand-green)" stroke-width="1.2"/></svg>@velmora.cabinets</li>
      </ul>
    </div>
  </section>

  <section class="business-card card-front">
    <div class="brand-name">Velmora<br>Cabinets</div>
    <div class="signature-divider"></div>
    <div class="person">
      <div class="full-name">Rowan Ashdale</div>
      <div class="role">Director Craftsman</div>
      <ul class="details">
        <li><svg class="icon" viewBox="0 0 10 10"><path d="M1 4c2-3 6-3 8 0l-1.5 1-1-1.2h-3L2.5 5z M2.5 5.5h5l1 3.5h-7z" fill="var(--brand-green)"/></svg>0412558301</li>
        <li><svg class="icon" viewBox="0 0 10 10"><rect x="0.5" y="2" width="9" height="6" fill="var(--brand-green)"/><path d="M0.5 2l4.5 3.5 4.5-3.5" stroke="var(--card-black)" stroke-width="0.8" fill="none"/></svg>info@velmoracabinets.com.au</li>
        <li><svg class="icon" viewBox="0 0 10 10"><circle cx="5" cy="5" r="3.8" fill="none" stroke="var(--brand-green)" stroke-width="1.2"/></svg>@velmora.cabinets</li>
      </ul>
    </div>
  </section>

  <section class="business-card card-back">
    <div class="brand-name">Velmora<br>Cabinets</div>
  </section>

</main>
</body>
</html>
```